mothers day ad for martial arts school

I am looking to have a nice flyer/handout to promote my martial arts school. It is for our promotion of "mom's train free" for mothers day in May. I would like an ad that would inspire a mother to learn self defense and to improve their fitness. It can have pictures but not necessarily a requirement. Pictures don't have to be of a lady in a martial arts uniform. It may be better if they are not. It also doesn't have to be standard sheet of paper size, as these are going to be handouts the size can be smaller. I would like our Copper Vale logo on the flyer.

Target Market(s)

mothers that hadn't thought about martial arts before but would be convinced to try it

Industry/Entity Type

School

Requirements
Must have
• text, photos that would appeal to and encourage a mother to try a self defense/fitness class
Nice to have
• our logo and text and possibly pictures that would inspire a mother to join a martial arts class

```html
<!DOCTYPE html>
<html lang="en">
<head>
<meta charset="utf-8">
<title>Mom's Train Free – Copper Vale Martial Arts</title>
<link rel="stylesheet" href="https://fonts.googleapis.com/css2?family=Kaushan+Script&family=Open+Sans:wght@400&family=Roboto+Condensed:ital,wght@0,700;0,900;1,700;1,900&family=Russo+One&display=block">
<style>
  :root {
    --red: #e41f26;
    --red-dark: #b5141a;
    --ink: #111111;
    --white: #ffffff;
    --paper: #eeeeee;
    --gold: #f5e400;
    --text: #222222;
  }
  * { margin: 0; padding: 0; box-sizing: border-box; }
  html, body { width: 822px; height: 1200px; overflow: hidden; background: var(--paper); }
  .flyer { position: relative; width: 822px; height: 1200px; overflow: hidden; background: var(--paper); }
  .flyer-art { position: absolute; inset: 0; }

  .headline {
    position: absolute; right: 44px; top: 16px; text-align: right;
    font-family: "Roboto Condensed", sans-serif; font-style: italic; font-weight: 900;
    color: var(--white); font-size: 94px; line-height: 84px; letter-spacing: -1px;
    text-shadow: 2px 3px 4px rgba(0,0,0,.45);
  }
  .headline-sub {
    position: absolute; right: 52px; top: 200px;
    font-family: "Kaushan Script", cursive; font-size: 30px; color: var(--gold);
    transform: rotate(-3deg); transform-origin: right center;
  }

  .badge {
    position: absolute; border-radius: 50%; display: flex; align-items: center; justify-content: center;
    text-align: center; font-family: "Roboto Condensed", sans-serif;
  }
  .badge-hours {
    left: 32px; top: 362px; width: 252px; height: 248px;
    background: radial-gradient(circle at 45% 30%, #f0474c, var(--red) 60%, var(--red-dark));
    color: var(--white); font-style: italic; font-weight: 900; font-size: 48px; line-height: 54px;
    text-shadow: 2px 2px 3px rgba(0,0,0,.35); box-shadow: 0 4px 10px rgba(0,0,0,.3);
  }
  .badge-skills {
    left: 470px; top: 634px; width: 274px; height: 268px;
    background: radial-gradient(circle at 50% 40%, #ffffff, #e6e6e6);
    border: 14px solid var(--red); color: var(--ink); font-weight: 900; font-size: 37px; line-height: 39px;
    box-shadow: 0 4px 10px rgba(0,0,0,.3);
  }

  .brand { position: absolute; left: 38px; top: 830px; display: flex; align-items: center; gap: 12px; }
  .brand-mark { width: 54px; height: 54px; border-radius: 50%; background: var(--red); }
  .brand-name {
    font-family: "Roboto Condensed", sans-serif; font-weight: 900; font-size: 56px; color: var(--ink);
    letter-spacing: 1px; text-transform: uppercase;
  }

  .banner {
    position: absolute; left: 37px; top: 917px; width: 747px; height: 32px;
    background: var(--red);
    display: flex; justify-content: space-between; align-items: center; padding: 0 20px 0 10px;
  }
  .banner-left { font-family: "Russo One", sans-serif; font-size: 23px; color: var(--white); }
  .banner-right { font-family: "Roboto Condensed", sans-serif; font-style: italic; font-weight: 700; font-size: 24px; color: var(--white); }

  .body-copy {
    position: absolute; left: 37px; top: 968px; width: 760px;
    font-family: "Open Sans", sans-serif; font-size: 17px; line-height: 25.5px; color: var(--text);
  }

  .web-label { position: absolute; left: 37px; top: 1120px; font-family: "Open Sans", sans-serif; font-size: 14px; color: var(--text); }
  .web-url {
    position: absolute; left: 37px; top: 1140px;
    font-family: "Roboto Condensed", sans-serif; font-style: italic; font-weight: 900; font-size: 29px; color: var(--ink);
  }

  .social { position: absolute; left: 470px; top: 1130px; display: flex; align-items: center; gap: 9px; }
  .social-label { font-family: "Kaushan Script", cursive; font-size: 24px; color: var(--red); margin-right: 8px; }
  .social-dot { width: 45px; height: 45px; border-radius: 50%; background: radial-gradient(circle at 40% 35%, #d0d0d0, #7a7a7a); border: 2px solid var(--white); box-shadow: 0 2px 4px rgba(0,0,0,.35); }
</style>
</head>
<body>
<main class="flyer">
  <svg class="flyer-art" width="822" height="1200" viewBox="0 0 822 1200">
    <defs>
      <linearGradient id="top-shade" x1="0" y1="0" x2="0" y2="1">
        <stop offset="0" stop-color="#555"/>
        <stop offset="1" stop-color="#9a9a9a"/>
      </linearGradient>
      <radialGradient id="photo-tone" cx="0.6" cy="0.5" r="0.65">
        <stop offset="0" stop-color="#d8b9a2"/>
        <stop offset="0.25" stop-color="#c4a58f"/>
        <stop offset="0.5" stop-color="#9e9a97"/>
        <stop offset="0.8" stop-color="#7c7c7c"/>
        <stop offset="1" stop-color="#5a5a5a"/>
      </radialGradient>
    </defs>
    <rect class="paper-base" x="0" y="0" width="822" height="1200" fill="#eeeeee"/>
    <rect class="top-field" x="0" y="0" width="822" height="690" fill="url(#top-shade)"/>
    <path class="swoosh-dark" d="M0 0 H160 C40 180 40 560 300 820 C200 780 80 700 0 600 Z" fill="#111"/>
    <path class="lower-field" d="M0 600 C120 720 280 820 500 830 C640 835 760 780 822 700 V1200 H0 Z" fill="#eeeeee"/>
    <ellipse class="hero-photo" role="img" aria-label="Photo of a woman in a white tank top throwing a punch in black boxing gloves, hair flying" cx="492" cy="400" rx="412" ry="392" fill="url(#photo-tone)"/>
    <ellipse class="hero-ring" cx="492" cy="400" rx="420" ry="400" fill="none" stroke="var(--red)" stroke-width="10"/>
  </svg>

  <h1 class="headline">MOM'S<br>TRAIN FREE</h1>
  <p class="headline-sub">for mothers day in May</p>

  <div class="badge badge-hours">24-hour<br>Fitness<br>Center</div>
  <div class="badge badge-skills">Learn Life<br>Skills<br>Through<br>Martial<br>Arts</div>

  <div class="brand">
    <span class="brand-mark"></span>
    <span class="brand-name">Copper Vale</span>
  </div>

  <div class="banner">
    <span class="banner-left">MARTIAL ARTS SCHOOL</span>
    <span class="banner-right">Mother to learn self defense</span>
  </div>

  <p class="body-copy">Lorem ipsum dolor sit amet, consectetur adipiscing elit, sed do eiusmod tempor incididunt ut labore et dolore magna aliqua. Ut enim ad minim veniam, quis nostrud exercitation ullamco laboris nisi ut aliquip ex ea commodo consequat. Duis aute irure dolor in reprehenderit in voluptate velit esse cillum dolore eu fugiat nulla pariatur. Excepteur sint occaecat cupidatat non proident, sunt in culpa qui officia deserunt mollit anim id est laborum.</p>

  <p class="web-label">Please vist my Website</p>
  <p class="web-url">www.coppervalemartialarts.com</p>

  <div class="social">
    <span class="social-label">Follow Us</span>
    <span class="social-dot"></span>
    <span class="social-dot"></span>
    <span class="social-dot"></span>
    <span class="social-dot"></span>
  </div>
</main>
</body>
</html>
```